Investment company needing business card

We are wanting a business card which looks sharp and easy on the eye. We are thinking of having a business card with the logo embossed on it, to really make it stand out. We will only have a small amount of information of the business card, person's name, position, email address and phone number

Contact Information for Business Card

Danielle Frost
Executive Assistant
+64 21 473 5162
danielf@harwickpartners.co.nz

Requirements
Must have
• Embossed logo
Should not have
• Not to be busy

```html
<!DOCTYPE html>
<html lang="en">
<head>
<meta charset="utf-8">
<title>Harwick Partners – Business Card</title>
<link href="https://fonts.googleapis.com/css2?family=Open+Sans:wght@400;600;700&display=swap" rel="stylesheet">
<style>
  :root {
    --backdrop: #e8e6e4;
    --card: #ffffff;
    --green: #1fb16f;
    --charcoal: #5f6062;
    --ink: #4a4b4d;
    --rule: #d4d4d4;
  }
  * { box-sizing: border-box; margin: 0; padding: 0; }
  html, body { width: 1200px; height: 997px; overflow: hidden; }
  body {
    background: var(--backdrop);
    font-family: "Open Sans", Arial, sans-serif;
    color: var(--ink);
    display: flex;
    flex-direction: column;
    align-items: center;
    justify-content: center;
    gap: 70px;
  }
  .card {
    position: relative;
    width: 630px;
    height: 360px;
    background: var(--card);
    box-shadow: 0 6px 18px rgba(0,0,0,0.12);
    overflow: hidden;
  }

  /* Front */
  .brand {
    position: absolute;
    left: 44px;
    top: 52px;
    display: flex;
    align-items: center;
    gap: 12px;
  }
  .brand-mark {
    width: 22px;
    height: 22px;
    background: var(--green);
  }
  .brand-name {
    font-weight: 700;
    font-size: 28px;
    letter-spacing: 1px;
    color: var(--green);
    text-transform: uppercase;
  }
  .header-rule {
    position: absolute;
    left: 44px;
    right: 0;
    top: 118px;
    height: 1px;
    background: var(--rule);
  }
  .person {
    position: absolute;
    right: 40px;
    top: 150px;
    text-align: right;
  }
  .person-name {
    font-weight: 700;
    font-size: 17px;
    color: var(--ink);
    text-transform: uppercase;
  }
  .person-role {
    font-size: 13px;
    color: var(--charcoal);
    margin-top: 1px;
  }
  .band {
    position: absolute;
    height: 9px;
  }
  .band-green { left: 50%; right: 0; top: 205px; background: var(--green); }
  .band-grey { left: 0; width: 50%; top: 305px; background: var(--charcoal); }
  .contacts {
    position: absolute;
    left: 44px;
    top: 228px;
    list-style: none;
    font-size: 14px;
    line-height: 22px;
    color: var(--ink);
  }
  .contacts li { display: flex; align-items: center; gap: 9px; }
  .contacts svg { width: 11px; height: 11px; fill: var(--green); flex: none; }

  /* Back */
  .back-name {
    position: absolute;
    left: 0;
    right: 0;
    top: 120px;
    display: flex;
    justify-content: center;
    align-items: center;
    gap: 14px;
  }
  .back-name .brand-mark { width: 30px; height: 30px; }
  .back-name .brand-name { font-size: 40px; }
  .card-back .band-green { top: 250px; }
  .card-back .band-grey { top: 290px; }
</style>
</head>
<body>

  <section class="card card-front" aria-label="Business card front">
    <div class="brand">
      <span class="brand-mark"></span>
      <span class="brand-name">Harwick Partners</span>
    </div>
    <div class="header-rule"></div>

    <div class="person">
      <p class="person-name">Danielle Frost</p>
      <p class="person-role">Executive Assistant</p>
    </div>

    <div class="band band-green"></div>

    <ul class="contacts">
      <li>
        <svg viewBox="0 0 24 24"><path d="M6.6 10.8a15.1 15.1 0 0 0 6.6 6.6l2.2-2.2c.3-.3.7-.4 1-.2 1.1.4 2.3.6 3.6.6.6 0 1 .4 1 1V20c0 .6-.4 1-1 1A17 17 0 0 1 3 4c0-.6.4-1 1-1h3.5c.6 0 1 .4 1 1 0 1.3.2 2.5.6 3.6.1.3 0 .7-.2 1l-2.3 2.2z"/></svg>
        +64 21 473 5162
      </li>
      <li>
        <svg viewBox="0 0 24 24"><path d="M2 5h20v14H2z M2 5l10 8 10-8" /></svg>
        danielf@harwickpartners.co.nz
      </li>
      <li>
        <svg viewBox="0 0 24 24"><circle cx="12" cy="12" r="10"/></svg>
        www.harwickpartners.co.nz
      </li>
    </ul>

    <div class="band band-grey"></div>
  </section>

  <section class="card card-back" aria-label="Business card back">
    <div class="back-name">
      <span class="brand-mark"></span>
      <span class="brand-name">Harwick Partners</span>
    </div>
    <div class="band band-green"></div>
    <div class="band band-grey"></div>
  </section>

</body>
</html>
```